Bluefern Business Services needs a new interactive and interesting website

We need an interesting, professional, modern and functional company website for Bluefern Business Services - a young IT Services company based out of Chennai, India.

Bluefern Business Services is a fully owned subsidiary of Marlow Goods, one of the world's leading direct to consumer wine merchant.

We already have a registered company logo which must feature in the website.

We conceive, design, develop, test, implement and support IT solutions across the entire Marlow Goods IT landscape. For ex : We currently run about 25 e-commerce websites for Marlow Goods on ATG and Dot Net.

We would like to see our corporate colors used in the website. (Burgundy wine and wine green - source: www.bluefernbs-site.com)

We are looking at this website to communicate a fun, friendly and professionally managed company - reaching out to career seekers, prospective customers and general public.

For reference - The company name 'Bluefern' is an inspiration from the Marlow Goods lineage.

The second image with the world map is stickered on our main entrance to the office, I am not sure where this can be used -just putting it out there..

Please note that there are only a few more days to submit designs for this contest  !

I would appreciate if you can help posting your designs in time for our review and consideration.

Thanks.

Reason: Thanks for your inputs. We have a number of designers and a lot to digest and work with in the past few days. There has been a rush of new designs in the last few days Hence we will require more time to process these and make our decision. Hence i am requesting the contest to be open for more days. Regards, Tarun

Target Market(s)

Prospective job seekers who want to know more about the company and also wish to apply for a job vacancy
People wanting to know more about the company in general and our progress
People who want to see what we offer and how we can help them too - prospective customers
Companies that are interested in our IT Captive journey and are looking for a business opportunity

Industry/Entity Type

E-Commerce

Requirements
Must have
• Log In/ Register facility acting as a Single Sign on for Intranet (Employees)

Facility to post job vacancies (with an expiry date) and enable people to apply for a role and upload their CV/Resume.

Facility to Review Job applications

Facility for website visitors to contact Bluefern business Services via an online 'Contact Us' form with a split of job seekers and business opportunities

Gallery facility to upload pictures regarding company events
Nice to have
• Less Cluttered and contemporary design
Some Wine/Vineyard inspirations will be good but not too much, the company is an IT services company

```html
<!DOCTYPE html>
<html lang="en">
<head>
<meta charset="utf-8">
<title>Bluefern Business Services</title>
<link href="https://fonts.googleapis.com/css2?family=Open+Sans:wght@400;600;700&display=swap" rel="stylesheet">
<style>
:root{
  --page-bg:#33373d;
  --card:#f7f7f7;
  --rule:#e2e2e2;
  --burgundy:#7c1240;
  --olive:#7b8a2c;
  --olive-dark:#66731f;
  --text:#444;
  --muted:#666;
  --field:#e6e6e6;
}
*{margin:0;padding:0;box-sizing:border-box}
html,body{width:841px;height:1200px;overflow:hidden}
body{background:var(--page-bg);font-family:"Open Sans",sans-serif;color:var(--text);position:relative}
.site{position:absolute;left:63px;top:26px;width:715px;height:1134px;background:var(--card);border-radius:6px}
.abs{position:absolute}
.rule{position:absolute;left:15px;width:686px;height:1px;background:var(--rule)}
.brand{left:14px;top:12px;display:flex;align-items:center;gap:8px;color:var(--burgundy);font-weight:600}
.brand-mark{width:30px;height:30px;border-radius:50%;background:var(--burgundy)}
.brand-text{font-size:22px;line-height:24px}
.nav{left:270px;top:35px;width:431px;height:32px;background:#fff;border:1px solid #ddd;box-shadow:0 1px 2px rgba(0,0,0,.08);display:flex;justify-content:space-around;align-items:center;font-size:10.5px;color:#333;padding:0 4px}
.slider{left:15px;top:100px;width:686px;height:300px;background:repeating-linear-gradient(45deg,#e4e4e4 0 1px,#f0f0f0 1px 3px);border:1px solid #ddd}
.slide-photo{left:13px;top:12px;width:659px;height:273px;background:linear-gradient(180deg,#5d6a77 0%,#8a96a2 45%,#d9dde2 100%)}
.caption{right:13px;top:190px;width:287px;height:32px;background:rgba(30,30,30,.85);color:#fff;font-size:20px;line-height:32px;text-align:center}
.dots{left:327px;top:290px;display:flex;gap:3px}
.dot{width:6px;height:6px;border-radius:50%;border:1px solid #aaa;background:#fff}
.dot.on{background:var(--burgundy);border-color:var(--burgundy)}
.tagline{left:15px;top:438px;width:686px;text-align:center;font-size:16px;line-height:21px;color:#444}
.tagline b{color:var(--burgundy);font-weight:600}
.register{left:15px;top:519px;width:686px;height:55px;background:#fff;border:1px solid #e4e4e4;box-shadow:0 1px 2px rgba(0,0,0,.1);border-radius:3px}
.field{position:absolute;top:13px;width:175px;height:28px;background:var(--field);font-size:9px;color:#999;padding:9px 7px}
.btn{background:linear-gradient(#8f9e3a,var(--olive-dark));color:#fff;font-weight:600;border:1px solid #5d6a1c;border-radius:2px;text-align:center}
.reg-btn{position:absolute;left:562px;top:13px;width:112px;height:29px;font-size:15px;line-height:27px}
h2{position:absolute;left:14px;font-size:14.5px;font-weight:600;color:#333}
.service{position:absolute;width:310px}
.svc-icon{position:absolute;left:0;top:0;width:36px;height:36px;background:#fff;border:1px solid #ddd;border-radius:4px;display:flex;align-items:center;justify-content:center}
.svc-body{position:absolute;left:47px;top:4px;width:270px}
.svc-title{font-size:12px;color:var(--olive);line-height:16px}
.svc-text{font-size:8.6px;color:var(--muted);line-height:12.8px;margin-top:2px}
.more{font-size:8.6px;color:#333;text-decoration:underline;line-height:13px}
.gallery-text{left:14px;top:889px;width:690px;font-size:8.6px;line-height:12.6px;color:var(--muted)}
.thumb{position:absolute;top:916px;width:155px;height:112px;background:#fff;border:1px solid #ddd;box-shadow:0 1px 2px rgba(0,0,0,.15);padding:3px}
.thumb div{width:100%;height:100%}
.upload{left:14px;top:1047px;width:117px;height:29px;font-size:13px;line-height:27px}
.copyright{left:15px;top:1108px;width:686px;text-align:center;font-size:9px;color:#666}
</style>
</head>
<body>
<div class="site">
  <div class="abs brand"><span class="brand-mark"></span><span class="brand-text">Bluefern<br>Business Services</span></div>
  <nav class="abs nav"><span>Home</span><span>About Us</span><span>Clients</span><span>Our Services</span><span>Careers</span><span>Contact Us</span></nav>
  <div class="rule" style="top:83px"></div>

  <div class="abs slider">
    <div class="abs slide-photo" role="img" aria-label="Team of professionals in a meeting around a conference table"></div>
    <div class="abs caption">A Young IT Services Company</div>
    <div class="abs dots"><span class="dot"></span><span class="dot on"></span><span class="dot"></span><span class="dot"></span><span class="dot"></span></div>
  </div>

  <div class="rule" style="top:427px"></div>
  <p class="abs tagline">Lorem Ipsum <b>Dolor Sit</b> Amet Consectetur Adipsicing Elit, Sed Do<br>Euismod Tempor Incidunt <b>Magna Aliqua</b>.</p>
  <div class="rule" style="top:496px"></div>

  <form class="abs register">
    <div class="field" style="left:14px">First Name</div>
    <div class="field" style="left:197px">Last Name</div>
    <div class="field" style="left:380px">Email</div>
    <div class="btn reg-btn">Register Here</div>
  </form>

  <div class="rule" style="top:598px"></div>
  <h2 style="top:610px">Our Services</h2>

  <div class="service" style="left:29px;top:644px">
    <div class="svc-icon"><svg width="22" height="18" viewBox="0 0 22 18"><path d="M2 5l9-4 9 4-9 4z M2 5v8l9 4 9-4V5" fill="#ddd" stroke="#ccc"/></svg></div>
    <div class="svc-body"><div class="svc-title">Packaged Applications</div><div class="svc-text">Lorem ipsum dolor sit amet, consectetur adipisicing elit, sed do eiusmod tempor incididunt ut labore et dolore magna aliqua...</div><div class="more">Read More</div></div>
  </div>
  <div class="service" style="left:381px;top:644px">
    <div class="svc-icon"><svg width="14" height="20" viewBox="0 0 14 20"><rect x="1" y="1" width="12" height="18" fill="#e2e2e2" stroke="#ccc"/><path d="M4 4h2M8 4h2M4 8h2M8 8h2M4 12h2M8 12h2" stroke="#bbb"/></svg></div>
    <div class="svc-body"><div class="svc-title">Enterprise Application Integration</div><div class="svc-text">Lorem ipsum dolor sit amet, consectetur adipisicing elit, sed do eiusmod tempor incididunt ut labore et dolore magna aliqua...</div><div class="more">Read More</div></div>
  </div>
  <div class="service" style="left:29px;top:725px">
    <div class="svc-icon"><svg width="14" height="20" viewBox="0 0 14 20"><rect x="1" y="1" width="12" height="18" rx="1" fill="#e2e2e2" stroke="#ccc"/><rect x="3" y="4" width="8" height="4" fill="#ccc"/></svg></div>
    <div class="svc-body"><div class="svc-title">Digital Commerce</div><div class="svc-text">Lorem ipsum dolor sit amet, consectetur adipisicing elit, sed do eiusmod tempor incididunt ut labore et dolore magna aliqua...</div><div class="more">Read More</div></div>
  </div>
  <div class="service" style="left:381px;top:725px">
    <div class="svc-icon"><svg width="22" height="22" viewBox="0 0 22 22"><circle cx="11" cy="11" r="7" fill="#e2e2e2" stroke="#ccc" stroke-width="3" stroke-dasharray="2 2"/><circle cx="11" cy="11" r="3" fill="#fff" stroke="#ccc"/></svg></div>
    <div class="svc-body"><div class="svc-title">Application Development &amp; Maintenance</div><div class="svc-text">Lorem ipsum dolor sit amet, consectetur adipisicing elit, sed do eiusmod tempor incididunt ut labore et dolore magna aliqua...</div><div class="more">Read More</div></div>
  </div>

  <div class="rule" style="top:814px"></div>
  <h2 style="top:830px">Our Gallery</h2>
  <p class="abs gallery-text">Lorem ipsum dolor sit amet, consectetur adipisicing elit, sed do eiusmod tempor incididunt ut labore et dolore magna aliqua. Ut enim ad minim veniam, quis nostrud exercitation ullamco laboris nisi ut aliquip ex ea commodo consequat. Duis aute irure dolor in reprehenderit in voluptate velit esse cillum dolore eu fugiat nulla pariatur...</p>

  <div class="thumb" style="left:15px"><div role="img" aria-label="Colleagues in discussion at an office desk" style="background:linear-gradient(135deg,#c9bfb4,#8a7e74)"></div></div>
  <div class="thumb" style="left:192px"><div role="img" aria-label="Business team seated around a meeting table" style="background:linear-gradient(180deg,#e8e8e8,#4a4a50)"></div></div>
  <div class="thumb" style="left:369px"><div role="img" aria-label="Hands holding a tablet showing a dashboard" style="background:linear-gradient(135deg,#6f7f8c,#c9d2d8)"></div></div>
  <div class="thumb" style="left:546px"><div role="img" aria-label="Developers working together at a laptop" style="background:linear-gradient(135deg,#5a5d66,#9a9ca2)"></div></div>

  <div class="abs btn upload">Upload Pictures</div>
  <div class="rule" style="top:1097px"></div>
  <p class="abs copyright">Copyright Bluefern Business Services Private Limited.</p>
</div>
</body>
</html>
```